We need a logo design that explain all the products we possess.
The main goal is to represent graphically all the logos, pointing to one single logo - Vellamor.
The descriptions are in french.
I have uploaded a file with 4 logos to use:
Vellamor (the logo that all the rest should be pointing to)
RTN
Ombrevik
TroupéLune
All logo must be used in the vector graphic format, the description file is in each folder, it's the description that should be next to the logo.

The main goal of this is to create a banner 10' x 11' (estimated)

Target Market(s)

Cities

Requirements
Must have
• All the logos in the zip file in vector graphic.
Nice to have
• A background
Should not have
• Do not use KOL logo, it's a mix with RTN, and Kol Blue/dark blue with inscription "RTN", Charging fees for a part of the picture is not ok!

```html
<!DOCTYPE html>
<html lang="fr">
<head>
<meta charset="utf-8">
<title>Vellamor – Portail et services</title>
<link rel="stylesheet" href="https://fonts.googleapis.com/css2?family=Open+Sans:wght@600;700;800&display=swap">
<style>
  :root {
    --page: #ffffff;
    --field: #4a72b4;
    --field-deep: #2a4577;
    --bubble: #ffffff;
    --ink-blue: #3d67b0;
    --ink-grey: #4d4d4d;
    --faint-blue: #2f9be0;
    --badge-green: #8cbf3f;
    --badge-pink: #c4358e;
    --badge-red: #c0392b;
    --badge-gold: #e3aa22;
  }
  html, body {
    margin: 0;
    padding: 0;
    width: 1200px;
    height: 1091px;
    overflow: hidden;
    background: var(--page);
  }
  .banner {
    position: relative;
    width: 1200px;
    height: 1091px;
    font-family: "Open Sans", Arial, sans-serif;
  }
  .banner svg {
    position: absolute;
    inset: 0;
  }
  .label {
    position: absolute;
    transform: translateX(-50%);
    text-align: center;
    white-space: nowrap;
  }
  .brand {
    color: var(--ink-blue);
    font-weight: 800;
    line-height: 1;
  }
  .caption {
    color: var(--ink-grey);
    font-weight: 700;
    line-height: 1.35;
  }
  .hub-brand { left: 800px; top: 386px; font-size: 42px; letter-spacing: 1px; }
  .hub-caption { left: 800px; top: 436px; font-size: 15px; }
  .rtn-brand { left: 396px; top: 400px; font-size: 28px; }
  .rtn-caption { left: 396px; top: 432px; font-size: 11.5px; }
  .pets-brand { left: 498px; top: 696px; font-size: 27px; }
  .pets-caption { left: 498px; top: 727px; font-size: 11.5px; }
  .land-brand { left: 786px; top: 793px; font-size: 23px; letter-spacing: 3px; }
  .land-caption { left: 786px; top: 820px; font-size: 12px; }
</style>
</head>
<body>
<main class="banner">
  <svg width="1200" height="1091" viewBox="0 0 1200 1091" aria-hidden="false">
    <defs>
      <linearGradient id="faintGlow" x1="0" y1="0" x2="0" y2="1">
        <stop offset="0" stop-color="#2aa3e6"/>
        <stop offset="1" stop-color="#7cc4ee"/>
      </linearGradient>
      <linearGradient id="pinkBadge" x1="0" y1="0" x2="1" y2="1">
        <stop offset="0" stop-color="#d94aa0"/>
        <stop offset="1" stop-color="#9e2a78"/>
      </linearGradient>
      <linearGradient id="redBadge" x1="0" y1="0" x2="1" y2="1">
        <stop offset="0" stop-color="#d9503e"/>
        <stop offset="1" stop-color="#a32d22"/>
      </linearGradient>
      <linearGradient id="goldBadge" x1="0" y1="0" x2="1" y2="1">
        <stop offset="0" stop-color="#f0c13a"/>
        <stop offset="1" stop-color="#cf8f14"/>
      </linearGradient>
      <linearGradient id="greenBadge" x1="0" y1="0" x2="1" y2="1">
        <stop offset="0" stop-color="#a3cf55"/>
        <stop offset="1" stop-color="#74a832"/>
      </linearGradient>
      <linearGradient id="peopleTone" x1="0" y1="0" x2="0" y2="1">
        <stop offset="0" stop-color="#5aa0dc"/>
        <stop offset="1" stop-color="#9aa3ad"/>
      </linearGradient>
      <linearGradient id="mapTone" x1="0" y1="0" x2="1" y2="1">
        <stop offset="0" stop-color="#bfe3f2"/>
        <stop offset="1" stop-color="#7fb6d8"/>
      </linearGradient>
      <linearGradient id="petTone" x1="0" y1="0" x2="0" y2="1">
        <stop offset="0" stop-color="#6ab4e6"/>
        <stop offset="1" stop-color="#2f86c8"/>
      </linearGradient>
    </defs>

    <!-- field -->
    <rect class="field" x="172" y="156" width="844" height="768" fill="var(--field)"/>

    <!-- faint background motifs -->
    <rect role="img" aria-label="Grand pictogramme de calendrier en filigrane" x="224" y="212" width="150" height="186" rx="22" fill="url(#faintGlow)" opacity="0.75"/>
    <ellipse role="img" aria-label="Grande empreinte de patte en filigrane" cx="330" cy="760" rx="92" ry="92" fill="url(#faintGlow)" opacity="0.8"/>
    <ellipse role="img" aria-label="Grand pictogramme de coureur en filigrane" cx="918" cy="730" rx="70" ry="110" fill="url(#faintGlow)" opacity="0.8"/>

    <!-- connectors -->
    <g class="connectors" stroke="#ffffff" stroke-width="7" fill="none">
      <line x1="480" y1="378" x2="640" y2="378"/>
      <line x1="658" y1="516" x2="560" y2="610"/>
      <line x1="790" y1="574" x2="790" y2="660"/>
    </g>

    <!-- shadows -->
    <g class="shadows" fill="var(--field-deep)">
      <path d="M622,388 A180,180 0 0 1 802,208 L966,208 Q982,208 982,224 L982,388 A180,180 0 0 1 622,388 Z"/>
      <circle cx="406" cy="388" r="120"/>
      <circle cx="508" cy="706" r="120"/>
      <circle cx="796" cy="784" r="120"/>
    </g>

    <!-- hub bubble -->
    <path class="hub" d="M612,380 A180,180 0 0 1 792,200 L956,200 Q972,200 972,216 L972,380 A180,180 0 0 1 612,380 Z" fill="var(--bubble)"/>
    <rect role="img" aria-label="Illustration de citoyens devant des immeubles" x="684" y="298" width="234" height="80" rx="6" fill="url(#peopleTone)"/>

    <!-- growth badge -->
    <circle cx="910" cy="262" r="30" fill="url(#greenBadge)"/>
    <polyline points="892,274 902,262 910,268 926,250" stroke="#fff" stroke-width="4" fill="none" stroke-linejoin="round" stroke-linecap="round"/>
    <polyline points="918,250 926,250 926,258" stroke="#fff" stroke-width="4" fill="none" stroke-linecap="round" stroke-linejoin="round"/>

    <!-- product bubbles -->
    <circle class="bubble" cx="396" cy="378" r="120" fill="var(--bubble)"/>
    <circle class="bubble" cx="498" cy="696" r="120" fill="var(--bubble)"/>
    <circle class="bubble" cx="786" cy="774" r="120" fill="var(--bubble)"/>

    <rect role="img" aria-label="Pictogramme de document numérique" x="362" y="310" width="64" height="84" rx="4" fill="#5b8fd0"/>
    <rect role="img" aria-label="Silhouettes d'un chien et d'un chat" x="452" y="604" width="64" height="80" rx="30" fill="url(#petTone)"/>
    <rect role="img" aria-label="Plan de ville avec repère" x="716" y="706" width="150" height="82" rx="6" fill="url(#mapTone)"/>

    <!-- link badges -->
    <circle cx="600" cy="376" r="40" fill="#ffffff"/>
    <circle cx="600" cy="376" r="33" fill="url(#pinkBadge)"/>
    <g stroke="#fff" stroke-width="3.5" fill="none">
      <rect x="585" y="364" width="30" height="26" rx="4"/>
      <line x1="585" y1="372" x2="615" y2="372"/>
      <line x1="592" y1="359" x2="592" y2="366"/>
      <line x1="608" y1="359" x2="608" y2="366"/>
    </g>
    <g fill="#fff">
      <rect x="590" y="377" width="5" height="4"/><rect x="598" y="377" width="5" height="4"/><rect x="606" y="377" width="5" height="4"/>
      <rect x="590" y="383" width="5" height="4"/><rect x="598" y="383" width="5" height="4"/>
    </g>

    <circle cx="658" cy="516" r="45" fill="#ffffff"/>
    <circle cx="658" cy="516" r="38" fill="url(#redBadge)"/>
    <g fill="#fff">
      <ellipse cx="658" cy="528" rx="13" ry="10"/>
      <ellipse cx="644" cy="512" rx="5" ry="6.5"/>
      <ellipse cx="653" cy="503" rx="5" ry="6.5"/>
      <ellipse cx="664" cy="503" rx="5" ry="6.5"/>
      <ellipse cx="673" cy="512" rx="5" ry="6.5"/>
    </g>

    <circle cx="790" cy="574" r="40" fill="#ffffff"/>
    <circle cx="790" cy="574" r="33" fill="url(#goldBadge)"/>
    <path d="M776,574 L790,574 M790,562 L804,574 L790,586" stroke="#fff" stroke-width="4" fill="none" stroke-linecap="round" stroke-linejoin="round"/>
  </svg>

  <div class="label brand hub-brand">VELLAMOR</div>
  <div class="label caption hub-caption">PORTAIL VELLAMOR 2.0</div>

  <div class="label brand rtn-brand">RTN</div>
  <div class="label caption rtn-caption">CONSEIL SANS PAPIER</div>

  <div class="label brand pets-brand">TroupéLune</div>
  <div class="label caption pets-caption">LICENCES POUR ANIMAUX</div>

  <div class="label brand land-brand">OMBREVIK</div>
  <div class="label caption land-caption">PERMIS • CARTE<br>INVENTAIRE • TAXES</div>
</main>
</body>
</html>
```